Business Card Design (NEW FILES)

ATTENTION: New vector files are available. Please update your design to reflect/use the new (better resolution) logo images.

Seeking a unique and professional business card design for a commercial drone photography/videography business. The layout should feature
the logo (attached) and include the following information:
Owen Tarrick
614-502-7738
www.skylarkreelworks.example
NRD Certified Remote Pilot

Owen Tarrick

```html
<!DOCTYPE html>
<html lang="en">
<head>
<meta charset="utf-8">
<title>Skylark Reelworks – Business Card</title>
<link rel="stylesheet" href="https://fonts.googleapis.com/css2?family=Open+Sans:wght@400;600;700&display=swap">
<style>
  :root {
    --backdrop: #222222;
    --card-navy: #1a1b4b;
    --ink-white: #ffffff;
    --accent-orange: #ef8a4b;
  }
  * { margin: 0; padding: 0; box-sizing: border-box; }
  html, body {
    width: 1200px;
    height: 780px;
    overflow: hidden;
    background: var(--backdrop);
    font-family: "Open Sans", Arial, sans-serif;
  }
  .canvas {
    position: relative;
    width: 1200px;
    height: 780px;
    display: flex;
    flex-direction: column;
    align-items: center;
    justify-content: center;
    gap: 40px;
  }
  .card {
    position: relative;
    width: 600px;
    height: 343px;
    background: var(--card-navy);
    overflow: hidden;
  }

  /* Front: brand side */
  .card--brand {
    display: flex;
    align-items: center;
    justify-content: center;
  }
  .brand-lockup {
    display: flex;
    align-items: center;
    gap: 14px;
  }
  .brand-dot {
    width: 22px;
    height: 22px;
    border-radius: 50%;
    background: var(--accent-orange);
    flex-shrink: 0;
  }
  .brand-name {
    color: var(--ink-white);
    font-weight: 400;
    font-size: 38px;
    letter-spacing: 3px;
    text-transform: uppercase;
    white-space: nowrap;
  }

  /* Back: contact side */
  .card--contact .brand-corner {
    position: absolute;
    left: 34px;
    top: 40px;
    display: flex;
    align-items: center;
    gap: 8px;
  }
  .card--contact .brand-corner .brand-dot { width: 12px; height: 12px; }
  .card--contact .brand-corner .brand-name { font-size: 18px; letter-spacing: 1.5px; }

  .contact-rail {
    position: absolute;
    top: 0;
    right: 0;
    width: 80px;
    height: 343px;
  }
  .person-name {
    position: absolute;
    right: 90px;
    top: 48px;
    font-size: 30px;
    font-weight: 700;
    letter-spacing: 0.5px;
    text-align: right;
    white-space: nowrap;
  }
  .person-name .first { color: var(--accent-orange); }
  .person-name .last { color: var(--ink-white); }
  .person-role {
    position: absolute;
    right: 90px;
    top: 92px;
    color: var(--ink-white);
    font-size: 15px;
    text-align: right;
  }
  .contact-details {
    position: absolute;
    right: 118px;
    top: 150px;
    list-style: none;
    color: var(--ink-white);
    font-size: 16px;
    line-height: 1.55;
    text-align: right;
    white-space: nowrap;
  }
</style>
</head>
<body>
<main class="canvas">

  <section class="card card--brand" aria-label="Card front">
    <div class="brand-lockup">
      <span class="brand-dot"></span>
      <span class="brand-name">Skylark Reelworks</span>
    </div>
  </section>

  <section class="card card--contact" aria-label="Card back">
    <div class="brand-corner">
      <span class="brand-dot"></span>
      <span class="brand-name">Skylark Reelworks</span>
    </div>

    <h1 class="person-name"><span class="first">Owen</span> <span class="last">Tarrick</span></h1>
    <p class="person-role">Owner</p>

    <ul class="contact-details">
      <li>614-502-7738</li>
      <li>www.skylarkreelworks.example</li>
      <li>NRD Certified Remote Pilot</li>
      <li>Fully Insured</li>
    </ul>

    <svg class="contact-rail" viewBox="0 0 80 343" aria-hidden="true">
      <line x1="44" y1="0" x2="44" y2="343" stroke="var(--accent-orange)" stroke-width="2.5"/>
      <!-- person marker -->
      <rect x="26" y="54" width="36" height="36" rx="4" fill="var(--accent-orange)" transform="rotate(45 44 72)"/>
      <circle cx="44" cy="66" r="5.5" fill="var(--card-navy)"/>
      <path d="M33 83 q11 -14 22 0 z" fill="var(--card-navy)"/>
      <!-- phone marker -->
      <rect x="33" y="158" width="22" height="22" rx="3" fill="var(--accent-orange)" transform="rotate(45 44 169)"/>
      <path d="M40 162 q-3 7 4 14 l3 -2 -2.5 -3 -2 1 q-2.5 -3 -1 -6 l2 -0.5 -0.5 -3.5 z" fill="var(--ink-white)"/>
      <!-- globe marker -->
      <rect x="33" y="184" width="22" height="22" rx="3" fill="var(--accent-orange)" transform="rotate(45 44 195)"/>
      <circle cx="44" cy="195" r="6" fill="none" stroke="var(--ink-white)" stroke-width="1.4"/>
      <ellipse cx="44" cy="195" rx="2.6" ry="6" fill="none" stroke="var(--ink-white)" stroke-width="1.1"/>
      <line x1="38" y1="195" x2="50" y2="195" stroke="var(--ink-white)" stroke-width="1.1"/>
      <!-- end marker -->
      <rect x="32" y="262" width="24" height="24" rx="3" fill="var(--accent-orange)" transform="rotate(45 44 274)"/>
    </svg>
  </section>

</main>
</body>
</html>
```